Moravel Aesthetic Doctor

I require an elegant, luxurious looking business card for my aesthetic business. I am a doctor and that will set me aside from competitors. I am planning to provide home and spa based treatments to clients with high expectations. I have attached my logo.

```html
<!DOCTYPE html>
<html lang="en">
<head>
<meta charset="utf-8">
<title>Moravel Aesthetic Doctor – Business Card</title>
<link href="https://fonts.googleapis.com/css2?family=Roboto:wght@300;400;500&display=swap" rel="stylesheet">
<style>
  :root {
    --backdrop: #c4c4c4;
    --card: #f1f1f1;
    --card-edge: #e4e4e4;
    --ink: #3d4147;
    --ink-soft: #70757c;
    --brand-grey: #8a8e95;
    --brand-blue: #3a8fd0;
    --band-deep: #1a67ae;
    --band-light: #4a9cd6;
    --rule: #9aa0a6;
  }
  * { box-sizing: border-box; margin: 0; padding: 0; }
  html, body { width: 1200px; height: 576px; overflow: hidden; }
  body {
    background: var(--backdrop);
    font-family: "Roboto", Arial, sans-serif;
    color: var(--ink);
    position: relative;
  }
  .card {
    position: absolute;
    top: 140px;
    width: 484px;
    height: 292px;
    border-radius: 10px;
    background: linear-gradient(180deg, #f7f7f7 0%, var(--card) 60%, var(--card-edge) 100%);
    overflow: hidden;
  }
  .card--front { left: 82px; }
  .card--back { left: 602px; }

  .brand { position: absolute; display: flex; align-items: center; }
  .brand__dot {
    border-radius: 50%;
    border: 2px solid var(--brand-grey);
    flex: none;
  }
  .brand__name {
    font-weight: 300;
    color: var(--brand-grey);
    line-height: 1;
    text-transform: uppercase;
    white-space: nowrap;
  }
  .brand__name span { display: block; }

  .card--front .brand { left: 106px; top: 57px; gap: 16px; }
  .card--front .brand__dot { width: 80px; height: 80px; }
  .card--front .brand__title { font-size: 46px; letter-spacing: 2px; }
  .card--front .brand__sub { font-size: 20px; letter-spacing: 2.4px; margin-top: 6px; }

  .card--back .brand { left: 18px; top: 29px; gap: 14px; }
  .card--back .brand__dot { width: 86px; height: 86px; }
  .card--back .brand__title { font-size: 44px; letter-spacing: 2px; }
  .card--back .brand__sub { font-size: 19px; letter-spacing: 2.3px; margin-top: 6px; }

  .services {
    position: absolute;
    left: 0; right: 0; top: 194px;
    text-align: center;
    font-size: 13px;
    line-height: 19px;
    color: var(--ink);
  }
  .services .sep { color: var(--brand-blue); margin: 0 7px; }

  .band {
    position: absolute;
    left: 0; right: 0; top: 239px; height: 34px;
    background: linear-gradient(90deg, var(--band-deep) 0%, var(--band-deep) 45%, var(--band-light) 100%);
    color: #fff;
    font-size: 12px;
    letter-spacing: 1.2px;
    text-transform: uppercase;
    display: flex; align-items: center; justify-content: center;
  }

  .silhouette-area {
    position: absolute;
    right: 0; top: 0; width: 190px; height: 292px;
    background: radial-gradient(ellipse at 65% 45%, rgba(200,203,207,0.55) 0%, rgba(220,222,224,0.25) 55%, rgba(241,241,241,0) 80%);
  }

  .doctor {
    position: absolute; left: 24px; top: 194px; right: 36px;
    display: flex; align-items: baseline; gap: 6px;
  }
  .doctor__name { font-size: 19px; font-weight: 400; color: var(--ink); white-space: nowrap; }
  .doctor__letters { font-size: 9.5px; color: var(--brand-blue); white-space: nowrap; }
  .doctor__rule { flex: 1; height: 1px; background: var(--rule); margin-left: 4px; align-self: center; }

  .qualification {
    position: absolute; left: 24px; top: 218px;
    font-size: 12.5px; color: var(--brand-blue);
  }

  .contacts {
    position: absolute; left: 22px; top: 243px;
    width: 376px;
    display: flex; align-items: center; gap: 9px;
    font-size: 12px; color: var(--ink);
    white-space: nowrap;
  }
  .contact { display: flex; align-items: center; gap: 5px; }
  .contact svg { width: 16px; height: 16px; flex: none; }
  .contact .accent { color: var(--brand-blue); }

  .social-pill {
    position: absolute; left: 408px; top: 242px;
    width: 76px; height: 20px;
    border-radius: 10px 0 0 10px;
    background: var(--band-light);
    display: flex; align-items: center; gap: 8px; padding-left: 14px;
  }
  .social-pill i { width: 9px; height: 9px; border-radius: 50%; background: #fff; display: block; }
</style>
</head>
<body>

<section class="card card--front" aria-label="Card front">
  <div class="brand">
    <span class="brand__dot"></span>
    <div class="brand__name">
      <span class="brand__title">Moravel</span>
      <span class="brand__sub">Aesthetic Doctor</span>
    </div>
  </div>
  <div class="services">
    <div>Dermal Injectables<span class="sep">|</span>Plasma Facials<span class="sep">|</span>Microneedling</div>
    <div>Skin Boosters<span class="sep">|</span>Excessive Sweating</div>
  </div>
  <div class="band">Home and Spa Based Treatments</div>
</section>

<section class="card card--back" aria-label="Card back">
  <div class="silhouette-area" role="img" aria-label="Faint decorative brand silhouette"></div>
  <div class="brand">
    <span class="brand__dot"></span>
    <div class="brand__name">
      <span class="brand__title">Moravel</span>
      <span class="brand__sub">Aesthetic Doctor</span>
    </div>
  </div>

  <div class="doctor">
    <span class="doctor__name">Dr Elin Varga</span>
    <span class="doctor__letters">MRCPCH MD</span>
    <span class="doctor__rule"></span>
  </div>
  <div class="qualification">Australasian Diploma of Aesthetic Medicine</div>

  <div class="contacts">
    <div class="contact">
      <svg viewBox="0 0 18 18" aria-hidden="true"><circle cx="9" cy="9" r="8" fill="none" stroke="#c9ccd0"/><path d="M6 4.8l1.6-.3 1 2.2-1 .9a6 6 0 0 0 2.8 2.8l.9-1 2.2 1-.3 1.6c-3.9.3-7.5-3.3-7.2-7.2z" fill="#3a8fd0"/></svg>
      <span>0800 555 018</span>
    </div>
    <div class="contact">
      <svg viewBox="0 0 18 18" aria-hidden="true"><circle cx="9" cy="9" r="8" fill="none" stroke="#c9ccd0"/><rect x="4.5" y="6" width="9" height="6.4" rx="0.6" fill="#3a8fd0"/><path d="M4.8 6.3L9 9.4l4.2-3.1" fill="none" stroke="#fff" stroke-width="0.9"/></svg>
      <span>elin@moravel.co.nz</span>
    </div>
    <div class="contact">
      <svg viewBox="0 0 18 18" aria-hidden="true"><circle cx="9" cy="9" r="8" fill="none" stroke="#c9ccd0"/><g fill="none" stroke="#3a8fd0" stroke-width="0.9"><circle cx="9" cy="9" r="4.6"/><ellipse cx="9" cy="9" rx="2" ry="4.6"/><path d="M4.4 9h9.2M5 6.8h8M5 11.2h8"/></g></svg>
      <span>www.<span class="accent">moravel</span>.co.nz</span>
    </div>
  </div>

  <div class="social-pill" aria-label="Social links"><i></i><i></i></div>
</section>

</body>
</html>
```